Etiketten für Honig
Wir können nur volle Punktzahl geben. Roswitha ist selbst Ideenreich, wirklich nett und setzte unsere Ideen schnell und engagiert um. Hat echt Spass gemacht mit ihr zu arbeiten.
Zielgruppe
Es scheint Missverständnisse zu geben weshalb ich das Briefing wohl ändern muss.
see below for English translation
Wir sind eine kleine Imkerei, die von der Liebhaberei in den Nebenerwerb wechselt. Wir verkaufen verschiedene Sortenhonige und Honigzubereitungen (siehe Webseite) im vorwiegend ländlichen Raum des Münsterlandes.
Entsprechend unseres Standortes und unserer Kundschaft benötigen wir ein klassisch ländliches Design. Hierfür haben wir auch bereits ein Logo welches verwendet werden muss.
English
There seems to be some misunderstanding, so I guess I'll have to change the briefing.
We are a small apiary that changes from hobby to sideline. We sell different types of honey and honey preparations (e.g. honey with raspberry) in a predominantly rural area of the Münsterland (Muensterland).
According to our location and our clientele, we need a classic rural design. We already have a logo which must be used.
Aufgabenstellung
Wir möchten ein rechteckiges Etikett mit Gewährverschluss das für verschiedene Sorten adoptierbar ist. Zum Beispiel durch den Austausch der Sortenbezeichnung und eine farbliche Veränderung.
Das Design soll später auf Naturpapier oder Graspapier gedruckt werden. Das Logo muss auf Etikett und Gewährverschluss abgebildet werden.
We would like a rectangular label with a guarantee seal that is adoptable for different varieties. For example, by exchanging the variety designation and changing the color.
The design will later be printed on uncoated paper or grass paper. The logo must be shown on the label and guarantee seal.

```html
<!DOCTYPE html>
<html lang="de">
<head>
<meta charset="utf-8">
<title>Etiketten Landhonig</title>
<link rel="stylesheet" href="https://fonts.googleapis.com/css2?family=Roboto+Condensed:wght@400;700&display=swap">
<style>
  :root {
    --bg: #ffffff;
    --kraft: #d9cbad;
    --kraft-light: #e6dcc4;
    --kraft-dark: #c9b891;
    --ink: #1f1f1f;
    --grey: #6d6e70;
    --yellow: #f6b21b;
    --yellow-light: #fbd67a;
    --green: #8cc63f;
    --green-light: #c3e39a;
    --paper: #ffffff;
  }
  * { box-sizing: border-box; margin: 0; padding: 0; }
  html, body { width: 1200px; height: 699px; overflow: hidden; background: var(--bg); }
  body { font-family: "Roboto Condensed", Arial, sans-serif; color: var(--ink); position: relative; }

  .abs { position: absolute; }

  /* guarantee seal */
  .seal-disc {
    left: 300px; top: 18px; width: 130px; height: 130px; border-radius: 50%;
    background: var(--yellow);
  }
  .seal-disc-inner {
    left: 318px; top: 36px; width: 94px; height: 94px; border-radius: 50%;
    background: var(--kraft-light);
    display: flex; align-items: center; justify-content: center;
    font-weight: 700; font-size: 10px; color: var(--grey); text-align: center; line-height: 1.1;
  }
  .seal-strip {
    left: 320px; top: 140px; width: 90px; height: 230px;
    background: linear-gradient(to bottom, var(--yellow) 0 52%, var(--kraft-light) 52% 100%);
  }
  .seal-strip-green {
    left: 935px; top: 270px; width: 80px; height: 100px;
    background: linear-gradient(to bottom, var(--green) 0 40%, var(--kraft-light) 40% 100%);
  }
  .seal-text {
    position: absolute; left: 0; right: 0; text-align: center;
    font-size: 10px; line-height: 1.15; text-transform: uppercase; color: var(--ink);
  }

  /* labels */
  .label { top: 370px; height: 250px; background: var(--kraft); overflow: hidden; }
  .label-main { left: 40px; width: 700px; }
  .label-variant { left: 800px; width: 360px; }

  .flap { left: 0; top: 0; width: 105px; height: 100%; background: var(--kraft-light); }
  .pattern {
    background: radial-gradient(ellipse at 20% 80%, var(--kraft-light), transparent 60%),
                radial-gradient(ellipse at 85% 70%, var(--kraft-light), transparent 55%),
                var(--kraft);
  }
  .panel { top: 0; height: 100%; }
  .panel-front { left: 105px; width: 410px; }
  .panel-info { left: 515px; width: 185px; background: var(--paper); padding: 14px 12px; font-size: 11.5px; line-height: 1.3; }

  .product-name {
    position: absolute; top: 28px; left: 0; right: 0; text-align: center;
    font-weight: 700; font-size: 20px; letter-spacing: 0.3px; color: var(--ink);
  }
  .tagline { left: 40px; top: 82px; width: 110px; height: 34px; border-radius: 4px; background: var(--kraft-dark); opacity: .6; }
  .brand-dot { left: 170px; top: 72px; width: 70px; height: 70px; border-radius: 50%; background: var(--yellow); }
  .brand-name {
    position: absolute; left: 0; right: 0; top: 150px; text-align: center;
    font-weight: 700; font-size: 26px; color: var(--grey); letter-spacing: 1px; line-height: 1;
  }
  .brand-name small { display: block; font-size: 13px; letter-spacing: 3px; margin-bottom: 4px; }

  .variety-band {
    position: absolute; left: 0; right: 0; bottom: 12px; height: 26px;
    display: flex; align-items: center; justify-content: center;
    font-weight: 700; font-size: 15px; letter-spacing: 1px; color: #fff;
  }
  .band-yellow { background: linear-gradient(to right, var(--yellow), var(--yellow-light)); }
  .band-green { background: linear-gradient(to right, var(--green), var(--green-light)); }

  .info-block { padding: 6px 0; border-bottom: 1px solid var(--ink); }
  .info-block:first-child { padding-top: 0; }
  .best-before { padding-top: 6px; }
  .date-box { margin-top: 4px; width: 110px; height: 18px; border: 1px solid var(--grey); background: #fff; }
  .weight { margin-top: 16px; font-size: 22px; }

  .panel-info-bg { background: var(--kraft-light); }
</style>
</head>
<body>

  <!-- left: unrolled label with seal -->
  <div class="abs seal-strip">
    <div class="seal-text" style="top:140px;">Deutscher<br>Honig</div>
  </div>
  <div class="abs seal-disc"></div>
  <div class="abs seal-disc-inner">BRINKHOVE</div>

  <div class="abs label label-main pattern">
    <div class="abs flap pattern" role="img" aria-label="Feines Blüten- und Gräsermuster auf Naturpapier"></div>

    <div class="abs panel panel-front" role="group">
      <div class="product-name">WIESENTHALER LANDHONIG</div>
      <div class="abs tagline" role="img" aria-label="Handschriftlicher Schriftzug: von Bienen aus dem Münsterland"></div>
      <div class="abs brand-dot"></div>
      <div class="brand-name"><small>HONIGMANUFAKTUR</small>BRINKHOVE</div>
      <div class="variety-band band-yellow">BLÜTENHONIG</div>
    </div>

    <div class="abs panel panel-info panel-info-bg">
      <div class="info-block">Trocken, Dunkel und vor Wärme geschützt lagern</div>
      <div class="info-block">Honigmanufaktur Brinkhove<br>Lindenweg 15<br>D-48163 Wiesenthal<br>honigmanufaktur-brinkhove.de</div>
      <div class="info-block">Mehrwegglas bitte an Imkerei zurückgeben</div>
      <div class="best-before">Mindestens haltbar bis:
        <div class="date-box"></div>
      </div>
      <div class="weight">500g</div>
    </div>
  </div>

  <!-- right: variant label -->
  <div class="abs seal-strip-green">
    <div class="seal-text" style="top:50px;">Deutscher<br>Honig</div>
  </div>
  <div class="abs label label-variant pattern">
    <div class="product-name">WIESENTHALER LANDHONIG</div>
    <div class="abs tagline" style="left:20px;" role="img" aria-label="Handschriftlicher Schriftzug: von Bienen aus dem Münsterland"></div>
    <div class="abs brand-dot" style="left:145px;"></div>
    <div class="brand-name"><small>HONIGMANUFAKTUR</small>BRINKHOVE</div>
    <div class="variety-band band-green">WALDHONIG</div>
  </div>

</body>
</html>
```